RWT Fittings Ltd Business Cards

We need a business card with our business logo. We provide window and door installations on high-rises in west coast British Colombia, Canada.

I would like my business information and details on one side of the card, and the other side the company name with logo

Target Market(s)

General Contractors

Industry/Entity Type

Construction

Contact Information for Business Card

one side i want my company name and logo in the dark theme logo that i provided

Requirements
Must have
• Marco Peltieri, 16045518293, RWTFittings@mailbox-demo.com, 1407-5194 Linden Row Burnaby BC, V5H 2K9, Owner & Manager

```html
<!DOCTYPE html>
<html lang="en">
<head>
<meta charset="utf-8">
<title>RWT Fittings Ltd – Business Cards</title>
<link rel="stylesheet" href="https://fonts.googleapis.com/css2?family=Open+Sans:wght@400;700&display=swap">
<style>
  :root {
    --backdrop: #3a3a3a;
    --card-dark: #1b1b1b;
    --brand-blue: #29a8e0;
    --text-light: #eeeeee;
    --text-muted: #bdbdbd;
  }
  * { box-sizing: border-box; margin: 0; padding: 0; }
  html, body { width: 1200px; height: 780px; overflow: hidden; }
  body {
    background: var(--backdrop);
    font-family: "Open Sans", Arial, sans-serif;
    position: relative;
  }
  .card {
    position: absolute;
    top: 230px;
    width: 530px;
    height: 310px;
    border-radius: 24px;
    overflow: hidden;
    box-shadow: 0 12px 30px rgba(0,0,0,.35);
  }
  .card--contact { left: 50px; background: var(--card-dark); color: var(--text-light); }
  .card--brand { left: 620px; background: var(--brand-blue); }

  .contact-name {
    position: absolute; left: 150px; top: 40px;
    font-size: 26px; font-weight: 700; color: var(--brand-blue);
    letter-spacing: 1px; text-transform: uppercase;
    display: flex; align-items: center; gap: 10px;
  }
  .brand-mark { width: 16px; height: 16px; background: var(--brand-blue); }
  .address {
    position: absolute; left: 110px; top: 92px;
    font-size: 13px; line-height: 1.45; color: var(--text-light);
  }
  .contact-list {
    position: absolute; left: 32px; top: 160px;
    list-style: none; font-size: 13px; line-height: 1.65;
  }
  .contact-list li { display: flex; align-items: center; gap: 8px; }
  .contact-list svg { width: 11px; height: 11px; fill: var(--brand-blue); flex: none; }
  .person {
    position: absolute; right: 34px; top: 168px; text-align: right;
  }
  .person-name {
    font-size: 19px; font-weight: 700; color: var(--brand-blue);
    text-transform: uppercase; letter-spacing: .5px;
  }
  .person-role { font-size: 14px; color: var(--text-light); }
  .edge-tab {
    position: absolute; right: 0; top: 168px;
    width: 14px; height: 52px; background: var(--brand-blue);
  }

  .brand-name {
    position: absolute; inset: 0;
    display: flex; align-items: center; justify-content: center; gap: 16px;
    font-size: 44px; font-weight: 700; color: #f2f2f2;
    text-transform: uppercase; letter-spacing: 2px;
  }
  .brand-name .brand-mark { width: 30px; height: 30px; background: #f2f2f2; }
</style>
</head>
<body>
  <section class="card card--contact" aria-label="Contact side">
    <div class="contact-name"><span class="brand-mark"></span>RWT Fittings Ltd</div>
    <p class="address">1407-5194 Linden Row<br>Burnaby BC, V5H 2K9</p>
    <ul class="contact-list">
      <li><svg viewBox="0 0 12 12"><path d="M2.5 0.5l2 2.2-1 1.2c.7 1.6 2 2.9 3.6 3.6l1.2-1 2.2 2-1.3 2.3C4.7 10.4 1.6 7.3.2 1.8z"/></svg>16045518293</li>
      <li><svg viewBox="0 0 12 12"><path d="M0 2h12v1L6 7 0 3zM0 4.3l6 4 6-4V10H0z"/></svg>RWTFittings@mailbox-demo.com</li>
      <li><svg viewBox="0 0 12 12"><circle cx="6" cy="6" r="5.5"/></svg>www.rwtfittings-demo.com</li>
    </ul>
    <div class="person">
      <p class="person-name">Marco Peltieri</p>
      <p class="person-role">Owner &amp; Manager</p>
    </div>
    <span class="edge-tab"></span>
  </section>

  <section class="card card--brand" aria-label="Brand side">
    <div class="brand-name"><span class="brand-mark"></span>RWT Fittings Ltd</div>
  </section>
</body>
</html>
```